executive development which breaks down traditional practices and thought processes

4 or 5 page website. Home page idea is fixed but needs creative execution to work {see attachment}, branding, as in corporate identity is in place and ready to go, (see attachment). Site needs to reflect the the market and typical participant, which are very high achievers up to and including Board Level Members in 'world leading company's'.

What we do is different, we are often copied, but without the success.

We require simple, slick impact, we have powerful messages that need to be supported by exquisite, simplistic design. We know we are the best out there and have kept our heads under water, but now is the time to start our expansion process.

We have copywriters briefed, and are liking what we read, so time to engage with designers who might like to 'wow' us, as well as our existing and potential clients.

Pages to include a standard landing/home page, about us, methodology, testimonials/awards and let's talk pages. Our philosophy is: opening minds to new ways of thinking, being, working and acting; to challenge long held business, management and leadership biases.

Our experiential learning technique is branded 'Tamarind' where we take people out of their comfort zone or into new & very different environments; to experience the way methodology and leadership techniques from uncomfortable encounters can be beneficial in big business strategic decision making, being more innovative and solving leadership & managerial challenges with new eyes (or a new perspective).

We will need to include video clips for awards we have won and testimonials from participants and company's alike. We work across the globe, the site needs to reflect this, without us looking like a huge corporate company, which we are not. We are small but pack a powerful punch, and that's the way we like it. Our clients don't see us as consultants or suppliers, more as the missing cog or the oil in the machine to get their executives to engage and deliver unorthodox thought processes which keep them at the forefront of their industries.

Both the copywriters and ourselves see typography being a crucial element to the impact of the site, so those designers with a passion in this area may well find our preference.

We are ready to go, good luck.

sorry guys missing the brief by a long way, we always said we were not looking for an off the shelf solution/concept which could be created on any 'sun pebble' like ortal and to be honest that's all we have received

Reason: designs miss the brief

Reason: We are not getting the desired simplistic landing page required.

```html
<!DOCTYPE html>
<html lang="en">
<head>
<meta charset="utf-8">
<title>Halden Executive development</title>
<link rel="stylesheet" href="https://fonts.googleapis.com/css2?family=Ubuntu:ital,wght@0,400;0,500;1,400&family=Arimo:wght@700&display=swap">
<style>
  :root {
    --violet: #4400ff;
    --green: #3af014;
    --green-dark: #22b400;
    --bar: rgba(48, 48, 50, 0.9);
    --bar-text: #f1f1f1;
    --grey-text: #6f6f6f;
    --rule: #8a8a8a;
    --white: #ffffff;
  }
  * { margin: 0; padding: 0; box-sizing: border-box; }
  html, body { width: 1200px; height: 1116px; overflow: hidden; }
  body {
    position: relative;
    font-family: "Ubuntu", sans-serif;
    background: #f3f3f3;
  }
  .backdrop {
    position: absolute; inset: 0 0 80px 0;
    background:
      radial-gradient(ellipse 260px 520px at 600px 480px, rgba(150,120,120,0.35), transparent 70%),
      linear-gradient(180deg, #f7f7f7 0%, #e4e4e4 40%, #d3d3d5 70%, #e9e9ea 100%);
  }
  .brand {
    position: absolute; left: 0; right: 0; top: 14px;
    text-align: center;
  }
  .brand-name {
    display: block;
    font-family: "Ubuntu", sans-serif; font-weight: 500;
    font-size: 104px; line-height: 108px; letter-spacing: 2px;
    color: var(--green);
  }
  .brand-tagline {
    display: block; margin-left: 200px;
    font-size: 20px; color: var(--grey-text);
  }
  .definitions { list-style: none; }
  .entry {
    position: absolute; left: 131px; width: 938px; height: 52px;
    top: calc(209px + var(--i) * 93.75px);
  }
  .entry-number {
    position: absolute; left: 0; top: -22px;
    width: 62px; height: 62px; border-radius: 50%;
    background: var(--green); border: 3px solid var(--green-dark);
    display: flex; align-items: center; justify-content: center;
  }
  .entry-number span {
    width: 38px; height: 38px; border-radius: 50%;
    background: #f2f2f2; color: #333;
    font-size: 24px; font-weight: 500;
    display: flex; align-items: center; justify-content: center;
  }
  .entry-text {
    position: absolute; left: 61px; right: 0; top: 0; bottom: 0;
    background: var(--bar); border-radius: 0 5px 5px 0;
    color: var(--bar-text); font-style: italic; font-size: 17px; line-height: 21px;
    padding: 0 20px; display: flex; align-items: center;
  }
  .part-label {
    position: absolute; left: 61px; top: -24px; height: 24px;
    background: var(--violet); color: var(--white);
    font-family: "Arimo", sans-serif; font-weight: 700; font-size: 16px;
    padding: 0 10px; line-height: 24px; border-radius: 3px 3px 0 0;
  }
  .sub-senses { list-style: none; position: absolute; left: 477px; top: 3px; }
  .sub-senses li { display: flex; align-items: center; gap: 8px; height: 22px; }
  .sub-senses b {
    width: 24px; height: 19px; border-radius: 10px 40% 40% 10px;
    background: var(--white); color: #222; font-style: normal;
    font-size: 14px; font-weight: 500; display: flex; align-items: center; justify-content: center;
  }
  .site-footer {
    position: absolute; left: 0; right: 0; top: 1035px; bottom: 0;
    background: var(--violet); border-top: 3px solid var(--rule);
    color: var(--white); text-align: center; font-size: 15px;
  }
  .footer-nav { margin-top: 14px; }
  .footer-nav a { color: var(--white); text-decoration: none; }
  .footer-nav .sep { margin: 0 7px; }
  .copyright { margin-top: 12px; }
</style>
</head>
<body>
  <div class="backdrop" role="img" aria-label="Misty photograph of a rowing crew on water, seen from behind"></div>

  <header class="brand">
    <span class="brand-name">halden</span>
    <span class="brand-tagline">Executive development</span>
  </header>

  <ol class="definitions">
    <li class="entry" style="--i:0">
      <div class="entry-number"><span>1</span></div>
      <div class="part-label">halden (hawl-den)</div>
      <p class="entry-text">The Act Or An Instance Of Looking For Or Seeking; Search: A Halden Fordiamonds.</p>
    </li>
    <li class="entry" style="--i:1">
      <div class="entry-number"><span>2</span></div>
      <p class="entry-text">(Historical Terms) (in Medieval Romance) An Expedition By Aknightor Company Of Knights To Accomplish Some Prescribed Task, Such Asfinding The Holy Grail</p>
    </li>
    <li class="entry" style="--i:2">
      <div class="entry-number"><span>3</span></div>
      <p class="entry-text">The Object Of A Search; Goal Or Target: My Halden Is The Treasure Ofthe King.</p>
    </li>
    <li class="entry" style="--i:3">
      <div class="entry-number"><span>4</span></div>
      <p class="entry-text">A Collection Of Alms</p>
    </li>
    <li class="entry" style="--i:4">
      <div class="entry-number"><span>5</span></div>
      <div class="part-label">vb (mainly intr)</div>
      <p class="entry-text">(foll By: For Or After) To Go In Search (of)</p>
    </li>
    <li class="entry" style="--i:5">
      <div class="entry-number"><span>6</span></div>
      <p class="entry-text">&nbsp;(Historical Terms) To Go On A Halden</p>
    </li>
    <li class="entry" style="--i:6">
      <div class="entry-number"><span>7</span></div>
      <div class="entry-text">
        <span>(Hunting) (of gun dogs or hounds)</span>
        <ul class="sub-senses">
          <li><b>a</b>To Search For Game</li>
          <li><b>b</b>To Bay When In Pursuit Of Game</li>
        </ul>
      </div>
    </li>
    <li class="entry" style="--i:7">
      <div class="entry-number"><span>8</span></div>
      <p class="entry-text">To Collect Alms</p>
    </li>
    <li class="entry" style="--i:8">
      <div class="entry-number"><span>9</span></div>
      <p class="entry-text">(also Tr) To Go In Search Of (a Thing); Seek Or Pursue</p>
    </li>
  </ol>

  <footer class="site-footer">
    <nav class="footer-nav">
      <a href="#">Home</a><span class="sep">|</span><a href="#">About Us</a><span class="sep">|</span><a href="#">Methodology</a><span class="sep">|</span><a href="#">Testimonials/awards</a><span class="sep">|</span><a href="#">Let's Talk</a>
    </nav>
    <p class="copyright">© 2014 HALDEN Executive development. All right reserved.</p>
  </footer>
</body>
</html>
```